Website for Dental Office - The Bright Arch Clinic

The bright arch clinic is a dental office offering cosmetic dentistry, general dentistry, and multi-specialty dental care all under one roof in our state-of-the-art cosmetic dental center. We are particularly striving to provide services that fit the need of the young generation. Thus, we hope to have a modern, professional concise website that represents our spirit.

*Should be able to switch from English to Chinese

6 sections besides homepage:
Home, Meet us, Services,
Patient Info, Cases&Reviews, Blog, Contact

The Services sections should contain multiple subsections such as cleaning and prevention, cosmetic dentistry, implant dentistry, removable dentures, etc...
The Patient Info section is also intended to contain several subsections such as
New Patient offer, accepted Insurance, patient portal, helpful tips, etc...

Target Market(s)

young generation

Coding

Coded - Design and coding required

Number of Pages Required

5+ page

Font styles to use
Sans Serif

Colors
0592cd
33a6d7
85cae6
00a990
33b8a4
86cfc6
cee9f5
cfeae6
3277b5

Requirements
Must have
• *Should be able to switch from English to Chinese
Nice to have
• http://www.thebrightarchclinic.com/
• As a reference, the above link is the current website, but we would like to change the appearance and the content (our new logo's picture is attached)

```html
<!DOCTYPE html>
<html lang="en">
<head>
<meta charset="utf-8">
<title>The Bright Arch Clinic</title>
<link href="https://fonts.googleapis.com/css2?family=Questrial&family=Nunito:wght@400;700;800;900&display=swap" rel="stylesheet">
<style>
:root{
  --blue:#0592cd;
  --blue-mid:#33a6d7;
  --blue-soft:#85cae6;
  --blue-pale:#cee9f5;
  --blue-deep:#3277b5;
  --brand:#1a7fc2;
  --teal:#00a990;
  --teal-mid:#33b8a4;
  --teal-soft:#86cfc6;
  --ice:#eef7fb;
  --text:#3c3c3c;
  --white:#ffffff;
}
*{margin:0;padding:0;box-sizing:border-box}
html,body{width:1200px;height:2620px;overflow:hidden}
body{position:relative;background:var(--white);font-family:"Questrial",sans-serif;color:var(--text)}
.abs{position:absolute}
a{color:inherit;text-decoration:none}

/* header */
.site-header{left:0;top:0;width:1200px;height:120px;background:var(--white)}
.brand{left:145px;top:32px;display:flex;align-items:center;gap:10px}
.brand-mark{width:30px;height:30px;border-radius:6px;background:var(--blue-mid)}
.brand-name{font-family:"Nunito",sans-serif;font-weight:800;font-size:17px;color:var(--brand);line-height:1.1}
.call{left:748px;top:22px;font-size:20px;color:var(--brand);display:flex;align-items:center;gap:8px}
.call b{font-family:"Nunito",sans-serif;font-weight:800}
.lang{left:1006px;top:26px;display:flex;align-items:center;gap:6px}
.lang-flag{width:32px;height:18px;background:var(--blue-deep);border:1px solid #c33}
.main-nav{left:404px;top:74px;display:flex;gap:34px;font-size:14px;color:#444;text-transform:uppercase}
.main-nav .active{color:var(--brand);font-family:"Nunito",sans-serif;font-weight:800}

/* hero */
.hero{left:0;top:120px;width:1200px;height:650px;background:linear-gradient(100deg,#7f8791 0%,#9ba2a9 45%,#d9c7c0 75%,#e8ddd8 100%)}
.hero-title{left:145px;top:250px;color:var(--white)}
.hero-title .light{font-size:52px;font-weight:400;letter-spacing:1px;display:block;line-height:1}
.hero-title .bold{font-family:"Nunito",sans-serif;font-weight:900;font-size:74px;display:block;line-height:1.2}
.hero-btn{left:145px;top:436px;width:220px;height:58px;border:2px solid var(--white);border-radius:30px;color:var(--white);font-family:"Nunito",sans-serif;font-weight:700;font-size:19px;display:flex;align-items:center;justify-content:center}
.dots{left:568px;top:618px;display:flex;gap:3px}
.dots span{width:13px;height:13px;border-radius:50%;border:2px solid var(--white)}
.dots span.on{background:var(--white)}
.hero-curve{left:0;top:655px}

/* intro */
.section-title{width:1200px;left:0;text-align:center;font-family:"Nunito",sans-serif;font-weight:900;font-size:37px;color:var(--brand);letter-spacing:.5px}
.intro-text{left:165px;width:870px;top:830px;text-align:center;font-size:12.6px;line-height:22px;color:#444}
.intro-text p{margin-bottom:14px}
.btn-solid{left:494px;top:1018px;width:214px;height:56px;border-radius:30px;background:var(--brand);color:var(--white);font-family:"Nunito",sans-serif;font-weight:800;font-size:14px;display:flex;align-items:center;justify-content:center}

/* services */
.services{left:0;top:1149px;width:1200px;height:574px;background:linear-gradient(135deg,#3a9ed6 0%,#2f92cf 50%,#3b9dd5 100%)}
.service{top:1302px;width:184px;text-align:center;color:var(--white)}
.service-card{margin:0 auto;display:block}
.service h3{font-family:"Nunito",sans-serif;font-weight:700;font-size:15.5px;margin-top:18px}
.service p{font-size:11.5px;line-height:19px;margin-top:14px;height:80px}
.pill{display:inline-flex;align-items:center;justify-content:center;width:127px;height:42px;border-radius:22px;font-family:"Nunito",sans-serif;font-weight:800;font-size:12px;margin-top:10px}
.pill-white{background:var(--white);color:var(--blue-mid)}
.pill-soft{background:var(--blue-soft);color:var(--white)}

/* patient info */
.patient{left:0;top:1723px;width:1200px;height:560px;background:var(--ice)}
.info{top:1876px;width:190px;text-align:center}
.info h3{font-family:"Nunito",sans-serif;font-weight:700;font-size:15px;color:#333;margin-top:18px}
.info p{font-size:11.5px;line-height:19px;color:#555;margin-top:12px;height:80px}
.pill-line{border:1.5px solid currentColor;background:transparent}

/* footer */
.footer-curve{left:0;top:2260px}
.footer{left:0;top:2330px;width:1200px;height:290px;background:var(--brand)}
.foot-head{top:2378px;font-family:"Nunito",sans-serif;font-weight:800;font-size:13.5px;color:var(--white);letter-spacing:.5px}
.foot-list{list-style:none;color:var(--white);font-size:12.5px}
.foot-list li{height:28px;display:flex;align-items:flex-start;gap:6px}
.dot-icon{width:11px;height:11px;border-radius:50%;background:var(--white);margin-top:3px;flex:none}
.foot-rule{left:145px;top:2566px;width:912px;height:1px;background:rgba(255,255,255,.35)}
.copyright{left:144px;top:2586px;font-size:12.5px;color:var(--white)}
.legal{left:866px;top:2587px;font-size:9.5px;color:var(--blue-soft)}
</style>
</head>
<body>

<header class="abs site-header">
  <a class="abs brand" href="#"><span class="brand-mark"></span><span class="brand-name">THE BRIGHT ARCH<br>CLINIC</span></a>
  <div class="abs call">
    <svg width="16" height="16" viewBox="0 0 24 24"><path fill="#1a7fc2" d="M6.6 10.8c1.4 2.8 3.8 5.1 6.6 6.6l2.2-2.2c.3-.3.7-.4 1-.2 1.1.4 2.3.6 3.6.6.6 0 1 .4 1 1V20c0 .6-.4 1-1 1C10.6 21 3 13.4 3 4c0-.6.4-1 1-1h3.5c.6 0 1 .4 1 1 0 1.3.2 2.5.6 3.6.1.3 0 .7-.2 1z"/></svg>
    <span>Call Us: <b>555.014.2273</b></span>
  </div>
  <div class="abs lang"><span class="lang-flag"></span>
    <svg width="10" height="6" viewBox="0 0 10 6"><path d="M0 0h10L5 6z" fill="#666"/></svg></div>
  <nav class="abs main-nav">
    <a class="active" href="#">Home</a><a href="#">Meet us</a><a href="#">Services</a><a href="#">Patient info</a><a href="#">Cases&amp;Reviews</a><a href="#">Blog</a><a href="#">Contact</a>
  </nav>
</header>

<section class="abs hero" role="img" aria-label="Close-up photo of a smiling mouth beside a tooth shade guide"></section>
<div class="abs hero-title"><span class="light">THE BRIGHT ARCH</span><span class="bold">CLINIC</span></div>
<a class="abs hero-btn" href="#">GET MORE INFO</a>
<div class="abs dots"><span class="on"></span><span></span><span></span><span></span></div>
<svg class="abs hero-curve" width="1200" height="120" viewBox="0 0 1200 120">
  <path d="M0 100 Q600 -40 1200 102 L1200 120 L0 120Z" fill="#cee9f5"/>
  <path d="M0 108 Q600 -30 1200 110 L1200 120 L0 120Z" fill="#ffffff"/>
</svg>

<h1 class="abs section-title" style="top:764px">YOUR SMILE. OUR PASSION.</h1>
<div class="abs intro-text">
  <p>Welcome to The Bright Arch Clinic where we specialize in General and Cosmetic Dentistry, Dental Implants, Periodontics (Gum Surgery), Endodontics (Root Canal Treatment) and Reconstructive Dentistry for patients in Boston, Brookline, Cambridge, Brighton, Allston, Newton, Watertown, Wellesley and all other surrounding neighborhoods of Boston, Massachusetts.</p>
  <p>With Northgate and Elmwood credentials that inspire confidence, we offer cosmetic dentistry, general dentistry and multi-specialty dental care all under one roof in our state-of-the-art cosmetic dental center conveniently located near Maple Square on Harbor Lane steps from the transit stop. Our specialist are also trained in providing Wrinkle Relaxers and Dermal Fillers and we would be honored to have you a part of our growing family.</p>
</div>
<a class="abs btn-solid" href="#">REQUEST APPOINTMENT</a>

<section class="abs services"></section>
<h2 class="abs section-title" style="top:1208px;color:#fff">OUR SERVICES</h2>

<div class="abs service" style="left:144px">
  <svg class="service-card" width="152" height="156" viewBox="0 0 152 156"><path d="M0 4Q0 0 4 0H148Q152 0 152 4V154Q76 100 0 154Z" fill="#fff"/><rect x="46" y="28" width="60" height="70" rx="10" fill="#e6f3fa" role="img" aria-label="Tooth with magnifier icon"/></svg>
  <h3>Cleaning and Prevention</h3>
  <p>Professional dental cleanings (oral prophylaxis) are usually performed by the dentist or a registered dental hygienist</p>
  <a class="pill pill-white" href="#">LEARN MORE</a>
</div>
<div class="abs service" style="left:387px">
  <svg class="service-card" width="152" height="156" viewBox="0 0 152 156"><path d="M0 4Q0 0 4 0H148Q152 0 152 4V154Q76 100 0 154Z" fill="#fff"/><rect x="36" y="38" width="80" height="44" rx="10" fill="#e6f3fa" role="img" aria-label="Smile with teeth icon"/></svg>
  <h3>Cosmetic Dentistry</h3>
  <p>Veneers are very thin pieces of durable, tooth shaped porcelain that are custom made and onded onto the front of teeth</p>
  <a class="pill pill-white" href="#">LEARN MORE</a>
</div>
<div class="abs service" style="left:630px">
  <svg class="service-card" width="152" height="156" viewBox="0 0 152 156"><path d="M0 4Q0 0 4 0H148Q152 0 152 4V154Q76 100 0 154Z" fill="#85cae6"/><rect x="46" y="24" width="60" height="76" rx="10" fill="#a6d8ee" role="img" aria-label="Dental implant icon"/></svg>
  <h3>Implant Dentistry</h3>
  <p>Dental implants are a great way to replace missing teeth and also provide a fixed solution to having removable partial or complete</p>
  <a class="pill pill-soft" href="#">LEARN MORE</a>
</div>
<div class="abs service" style="left:873px">
  <svg class="service-card" width="152" height="156" viewBox="0 0 152 156"><path d="M0 4Q0 0 4 0H148Q152 0 152 4V154Q76 100 0 154Z" fill="#fff"/><rect x="36" y="22" width="80" height="78" rx="10" fill="#e6f3fa" role="img" aria-label="Removable denture icon"/></svg>
  <h3>Removable Dentures</h3>
  <p>Removable partial dentures are used when only a few teeth are missing and there are still natural teeth present in the mouth.</p>
  <a class="pill pill-white" href="#">LEARN MORE</a>
</div>

<section class="abs patient"></section>
<h2 class="abs section-title" style="top:1788px">PATIENT INFO</h2>

<div class="abs info" style="left:136px">
  <svg width="190" height="166" viewBox="0 0 190 166" role="img" aria-label="Photo of a mother and daughter smiling together"><defs><linearGradient id="g1" x1="0" y1="0" x2="1" y2="1"><stop offset="0" stop-color="#e9ecef"/><stop offset="1" stop-color="#c7a58e"/></linearGradient></defs><path d="M17 10Q17 2 25 2H165Q173 2 173 10V162Q95 115 17 162Z" fill="url(#g1)" stroke="#85cae6" stroke-width="4"/></svg>
  <h3>New Patient offer</h3>
  <p>Thank you for your trust in us. We look forward to working with you towards a healthy and beautiful smile.</p>
  <a class="pill pill-line" style="color:#33a6d7" href="#">LEARN MORE</a>
</div>
<div class="abs info" style="left:382px">
  <svg width="190" height="166" viewBox="0 0 190 166" role="img" aria-label="Photo of a hand placing a wooden insurance block"><defs><linearGradient id="g2" x1="0" y1="0" x2="0" y2="1"><stop offset="0" stop-color="#3a302a"/><stop offset="1" stop-color="#b58d55"/></linearGradient></defs><path d="M17 10Q17 2 25 2H165Q173 2 173 10V162Q95 115 17 162Z" fill="url(#g2)" stroke="#86cfc6" stroke-width="4"/></svg>
  <h3>Accepted Insurance</h3>
  <p>Thank you for your trust in us. We look forward to working with you towards a healthy and beautiful smile.</p>
  <a class="pill pill-line" style="color:#00a990" href="#">LEARN MORE</a>
</div>
<div class="abs info" style="left:628px">
  <svg width="190" height="166" viewBox="0 0 190 166" role="img" aria-label="Photo of a patient at a dental checkup"><defs><linearGradient id="g3" x1="0" y1="0" x2="1" y2="1"><stop offset="0" stop-color="#c9ccd0"/><stop offset="1" stop-color="#8a6656"/></linearGradient></defs><path d="M17 10Q17 2 25 2H165Q173 2 173 10V162Q95 115 17 162Z" fill="url(#g3)" stroke="#cee9f5" stroke-width="4"/></svg>
  <h3>Patient Portal</h3>
  <p>Thank you for your trust in us. We look forward to working with you towards a healthy and beautiful smile.</p>
  <a class="pill pill-line" style="color:#85cae6" href="#">LEARN MORE</a>
</div>
<div class="abs info" style="left:874px">
  <svg width="190" height="166" viewBox="0 0 190 166" role="img" aria-label="Photo of a dental jaw model held in gloved hands"><defs><linearGradient id="g4" x1="0" y1="0" x2="1" y2="1"><stop offset="0" stop-color="#dfe7ef"/><stop offset="1" stop-color="#e26b72"/></linearGradient></defs><path d="M17 10Q17 2 25 2H165Q173 2 173 10V162Q95 115 17 162Z" fill="url(#g4)" stroke="#86cfc6" stroke-width="4"/></svg>
  <h3>Helpful Tips</h3>
  <p>Thank you for your trust in us. We look forward to working with you towards a healthy and beautiful smile.</p>
  <a class="pill pill-line" style="color:#33b8a4" href="#">LEARN MORE</a>
</div>

<svg class="abs footer-curve" width="1200" height="80" viewBox="0 0 1200 80">
  <path d="M0 12 Q600 140 1200 12 L1200 80 L0 80Z" fill="#85cae6"/>
  <path d="M0 20 Q600 140 1200 20 L1200 80 L0 80Z" fill="#1a7fc2"/>
</svg>
<footer class="abs footer"></footer>
<h4 class="abs foot-head" style="left:144px">QUICK LINKS</h4>
<h4 class="abs foot-head" style="left:576px">CONTACT INFO</h4>
<h4 class="abs foot-head" style="left:925px">CONNECT WITH US</h4>
<ul class="abs foot-list" style="left:144px;top:2423px"><li>Home</li><li>Meet us</li><li>Services</li><li>Patient Info</li></ul>
<ul class="abs foot-list" style="left:368px;top:2423px"><li>Cases&amp;Reviews</li><li>Blog</li><li>Contact</li></ul>
<ul class="abs foot-list" style="left:576px;top:2423px">
  <li style="height:50px"><svg width="10" height="13" viewBox="0 0 10 13" style="margin-top:3px"><path d="M5 0a5 5 0 0 1 5 5c0 3-5 8-5 8S0 8 0 5a5 5 0 0 1 5-5z" fill="#fff"/><circle cx="5" cy="5" r="2" fill="#1a7fc2"/></svg><span>275 Harbor Lane, Suite 12,<br>Brookline MA 02400</span></li>
  <li style="height:34px"><svg width="11" height="11" viewBox="0 0 24 24" style="margin-top:3px"><path fill="#fff" d="M6.6 10.8c1.4 2.8 3.8 5.1 6.6 6.6l2.2-2.2c.3-.3.7-.4 1-.2 1.1.4 2.3.6 3.6.6.6 0 1 .4 1 1V20c0 .6-.4 1-1 1C10.6 21 3 13.4 3 4c0-.6.4-1 1-1h3.5c.6 0 1 .4 1 1 0 1.3.2 2.5.6 3.6.1.3 0 .7-.2 1z"/></svg>555.014.2273</li>
  <li><svg width="12" height="9" viewBox="0 0 12 9" style="margin-top:4px"><rect width="12" height="9" fill="#fff"/><path d="M0 0l6 5 6-5" stroke="#1a7fc2" fill="none"/></svg>info@thebrightarchclinic.com</li>
</ul>
<ul class="abs foot-list" style="left:925px;top:2423px">
  <li><span class="dot-icon"></span>Microblog</li><li><span class="dot-icon"></span>Social Page</li><li><span class="dot-icon"></span>Photo Feed</li><li><span class="dot-icon"></span>Community</li>
</ul>
<div class="abs foot-rule"></div>
<p class="abs copyright">Copyrights © 2019 The Bright Arch Clinic. All rights reserved.</p>
<p class="abs legal">Terms and Conditions &nbsp;|&nbsp; Privacy Policy</p>

</body>
</html>
```